Plumbing company needs Business Card Design

Hi I need business card design based on logo which I uploaded. Its plumbing and heating company called Kranex Usługi Hydrauliczno-Gazowe. I want to see on my card motto of my company which is "...od wymiany uszczelki po wymiane łazienki.", my phone number, name, and website: 612478390, Marek Olejnik, info@kranex-inst.org, www.kranex-inst.org
I want to see logos of companys which I'm approved installer (Termova) (Le Valmont) (Korvo) (Plumox).
I want new creative look of business card. I like rounded corners.
Any questions please send message.
Thanks for intrest.
Industry/Entity Type
Business
Contact Information for Business Card
Marek Olejnik
612 478 390
info@kranex-inst.org
www.kranex-inst.org
...od wymiany uszczelki po wymiane łazienki.

```html
<!DOCTYPE html>
<html lang="pl">
<head>
<meta charset="utf-8">
<title>Kranex – wizytówka</title>
<link href="https://fonts.googleapis.com/css2?family=Roboto+Condensed:ital,wght@0,400;0,700;0,900;1,700;1,900&display=swap" rel="stylesheet">
<style>
  :root{
    --bg:#ece8e2;
    --card-white:#ffffff;
    --brand-red:#e02a36;
    --brand-blue:#2f5aa8;
    --brand-yellow:#f2ea2c;
    --yellow-deep:#dcd21e;
    --ink:#141414;
    --muted:#444444;
  }
  *{margin:0;padding:0;box-sizing:border-box}
  html,body{width:1200px;height:885px;overflow:hidden}
  body{background:var(--bg);font-family:"Roboto Condensed",Arial,sans-serif;position:relative}

  .card{position:absolute;top:62px;width:440px;height:760px;border-radius:26px;overflow:hidden;box-shadow:0 10px 30px rgba(0,0,0,.18)}
  .card--front{left:120px;background:var(--card-white)}
  .card--back{left:640px;background:linear-gradient(160deg,var(--brand-yellow),var(--yellow-deep))}

  /* front */
  .brand{position:absolute;top:54px;left:40px;right:40px;display:flex;align-items:center;gap:18px}
  .brand__mark{width:118px;height:118px;border-radius:18px;border:7px solid var(--brand-red);background:var(--brand-yellow);flex:none}
  .brand__name{font-weight:900;font-size:78px;line-height:1;color:var(--brand-red);letter-spacing:-1px}
  .brand__tagline{position:absolute;top:186px;left:40px;right:40px;text-align:right;font-weight:400;font-size:21px;color:var(--brand-blue)}
  .motto{position:absolute;top:218px;left:40px;right:40px;text-align:right;font-weight:700;font-size:19px;color:var(--brand-blue)}

  .person{position:absolute;top:286px;left:0;right:0;text-align:center;font-weight:900;font-style:italic;font-size:44px;color:var(--brand-blue)}
  .contact{position:absolute;top:366px;left:0;right:0;text-align:center;font-weight:900;font-style:italic;color:var(--brand-red);line-height:1.12}
  .contact__phone{font-size:44px;display:block}
  .contact__email{font-size:38px;display:block}

  .partners{position:absolute;top:496px;left:34px;right:34px;list-style:none;display:grid;grid-template-columns:auto auto auto;justify-content:space-between;align-items:start;row-gap:18px}
  .partner{font-weight:700;line-height:1;display:flex;align-items:center;gap:10px;white-space:nowrap}
  .partner--valmont{grid-column:1 / -1;justify-self:center;font-size:34px;color:var(--ink)}
  .partner--valmont .chip{width:30px;height:30px;border-radius:50%;background:var(--brand-blue)}
  .partner--termova{flex-direction:column;align-items:flex-start;gap:4px;font-size:30px;color:var(--ink)}
  .partner__sub{font-size:15px;font-weight:400;color:var(--muted)}
  .partner--korvo{font-size:32px;color:var(--brand-blue);padding-top:10px}
  .partner--plumox{font-size:26px;color:var(--ink);padding-top:22px}
  .partner--plumox .chip{width:24px;height:24px;background:var(--brand-yellow)}

  .web-band{position:absolute;left:0;right:0;bottom:0;height:88px;background:var(--brand-red);display:flex;align-items:center;justify-content:center}
  .web-band__url{color:#fff;font-weight:900;font-style:italic;font-size:40px}

  /* back */
  .back__content{position:absolute;top:50%;left:50%;width:760px;height:440px;transform:translate(-50%,-50%) rotate(90deg);display:flex;flex-direction:column;align-items:center;justify-content:center}
  .back__name{font-weight:900;font-size:190px;line-height:.95;color:var(--brand-red);letter-spacing:-3px}
  .back__tagline{font-weight:700;font-size:44px;color:var(--brand-blue);margin-top:6px}
</style>
</head>
<body>

<section class="card card--front" aria-label="Przód wizytówki">
  <header class="brand">
    <div class="brand__mark" role="img" aria-label="Ilustracja hydraulika w logo firmy"></div>
    <span class="brand__name">Kranex</span>
  </header>
  <p class="brand__tagline">Usługi Hydrauliczno-Gazowe</p>
  <p class="motto">...od wymiany uszczelki po wymiane łazienki.</p>

  <h1 class="person">Marek Olejnik</h1>
  <p class="contact">
    <span class="contact__phone">612 478 390</span>
    <span class="contact__email">info@kranex-inst.org</span>
  </p>

  <ul class="partners" aria-label="Autoryzowany instalator">
    <li class="partner partner--valmont">Le Valmont <span class="chip"></span></li>
    <li class="partner partner--termova">Termova<span class="partner__sub">Grupa Orvan</span></li>
    <li class="partner partner--korvo">Korvo</li>
    <li class="partner partner--plumox"><span class="chip"></span>Plumox</li>
  </ul>

  <footer class="web-band"><span class="web-band__url">www.kranex-inst.org</span></footer>
</section>

<section class="card card--back" aria-label="Tył wizytówki">
  <div class="back__content">
    <span class="back__name">Kranex</span>
    <span class="back__tagline">Usługi Hydrauliczno-Gazowe</span>
  </div>
</section>

</body>
</html>
```